Quillbrookes websites redesign

Www.quill-brookes.com needs to be redesigned along with updations. The incremental material will be provided for the updations. We are looking for complete redesign of the pages with the new content. The complete write up will be provided soon

Target Market(s)

Global

Coding

Coded - Design and coding required

Number of Pages Required

5+ page

Requirements
Must have
• A clean and slick design for the Consulting.
Should not have
• Too many pictures which reduces the speed of the site

```html
<!DOCTYPE html>
<html lang="en">
<head>
<meta charset="utf-8">
<title>Quillbrookes Consultancy</title>
<link href="https://fonts.googleapis.com/css2?family=Raleway:wght@300;400;500;600;700&family=Lora:ital@1&display=swap" rel="stylesheet">
<style>
:root{
  --accent:#2a9fd6;
  --ink:#444;
  --muted:#777;
  --rule:#d9d9d9;
  --grey-band:#f4f4f4;
  --footer:#1b1b1b;
  --footer-bottom:#151515;
  --footer-text:#a9a9a9;
}
*{margin:0;padding:0;box-sizing:border-box}
html,body{width:984px;height:1200px;overflow:hidden}
body{position:relative;background:#fff;font-family:Arial,Helvetica,sans-serif;color:var(--ink)}
.abs{position:absolute}

/* header */
.site-header{left:0;top:0;width:984px;height:54px;background:#fff}
.brand{left:220px;top:14px;display:flex;align-items:center;gap:7px;font-family:'Raleway',sans-serif;font-weight:500;font-size:19px;color:#333}
.brand-dot{width:22px;height:22px;border-radius:50%;background:#2d4d7a}
.main-nav{right:25px;top:0;display:flex;height:54px}
.main-nav a{font-family:'Raleway',sans-serif;font-size:8.5px;color:#555;text-decoration:none;line-height:54px;padding:0 8px;position:relative}
.main-nav a.active{color:var(--accent)}
.main-nav a.active::after{content:"";position:absolute;left:10px;right:10px;bottom:0;height:2px;background:var(--accent)}

/* hero */
.hero{left:0;top:54px;width:984px;height:268px;background:#000}
.hero-visual{left:230px;top:0;width:490px;height:268px;background:radial-gradient(ellipse 60% 55% at 50% 42%,#4aa6ff 0%,#1e5fc0 28%,#0b2c6a 55%,#000 85%)}
.hero-title{left:0;width:984px;top:109px;text-align:center;font-family:'Raleway',sans-serif;font-weight:300;font-size:18.5px;color:#fff}
.hero-sub{left:0;width:984px;top:144px;text-align:center;font-weight:700;font-size:8px;line-height:12px;color:#fff}
.hero-arrow{top:126px}
.hero-dots{left:475px;top:284px;display:flex;gap:3px}
.hero-dots span{width:6px;height:6px;border-radius:50%;border:1px solid #fff}
.hero-dots span.on{background:#fff}

/* welcome */
.welcome{left:0;width:984px;top:366px;text-align:center}
.welcome h1{font-family:'Raleway',sans-serif;font-weight:400;font-size:13.5px;color:#444;letter-spacing:.3px}
.welcome h1 b{font-weight:700}
.welcome .tagline{margin-top:8px;font-size:6.5px;color:#444}
.welcome .tagline span{color:var(--accent)}
.welcome .divider{width:30px;height:1px;background:#bbb;margin:9px auto 15px}
.welcome .intro{width:345px;margin:0 auto;font-size:6.8px;line-height:11px;color:#555}
.btn-contact{display:inline-block;margin-top:18px;border:1px solid #ccc;padding:6px 11px;font-size:6.5px;color:#555}

/* services */
.service{top:528px;width:120px;text-align:center}
.service .icon{height:32px;display:flex;justify-content:center;align-items:center}
.service h3{margin-top:13px;font-family:'Raleway',sans-serif;font-weight:500;font-size:8.8px;color:#444;padding-bottom:8px;border-bottom:1px solid var(--rule)}
.service.active h3{color:var(--accent)}
.service p{margin-top:7px;font-size:6.3px;line-height:12px;color:#777}
.service .more{display:inline-block;margin-top:7px;font-family:'Lora',serif;font-style:italic;font-size:7px;color:#999;padding-bottom:3px}
.service.active .more{color:var(--accent);border-bottom:1px solid var(--accent)}

/* consultancy band */
.consult-band{left:0;top:694px;width:984px;height:289px;background:var(--grey-band)}
.band-heading{left:220px;top:733px;width:542px;height:12px}
.band-heading::before{content:"";position:absolute;left:0;right:0;top:6px;height:1px;background:#ddd}
.band-heading h2{position:relative;width:100px;margin:0 auto;background:var(--grey-band);text-align:center;font-family:'Raleway',sans-serif;font-weight:500;font-size:11px;color:#666}
.card{top:777px;width:171px}
.card .photo{width:171px;height:100px;position:relative}
.card .go{position:absolute;right:0;bottom:0;width:19px;height:16px;background:#333;color:#fff;font-size:9px;text-align:center;line-height:16px}
.card .go.light{background:#fff;color:#333}
.card h4{margin-top:15px;font-family:'Raleway',sans-serif;font-weight:700;font-size:7.4px;color:#444;letter-spacing:.3px}
.card.active h4{color:var(--accent)}
.card p{margin-top:7px;font-size:6.5px;line-height:12px;color:#777}

/* footer */
.site-footer{left:0;top:983px;width:984px;height:217px;background:var(--footer)}
.footer-bottom{left:0;top:1168px;width:984px;height:32px;background:var(--footer-bottom);border-top:1px solid #2a2a2a}
.footer-bottom p{padding:15px 0 0 220px;font-size:6.8px;color:#888}
.f-brand{left:221px;top:1022px;display:flex;align-items:center;gap:6px;font-family:'Raleway',sans-serif;font-weight:500;font-size:14px;color:#9a9a9a}
.f-brand i{width:17px;height:17px;border-radius:50%;background:#888;display:block}
.f-address{left:221px;top:1054px;font-size:6.8px;line-height:12px;color:var(--footer-text)}
.f-contact{left:221px;top:1112px;font-size:7px;line-height:12.5px;color:var(--footer-text)}
.f-contact b{color:var(--accent)}
.f-contact u{color:var(--accent)}
.f-title{top:1024px;font-family:'Raleway',sans-serif;font-weight:600;font-size:8px;color:#eee;letter-spacing:.3px}
.f-title::after{content:"";display:block;width:17px;height:1px;background:#777;margin-top:8px}
.f-note{left:395px;top:1055px;font-size:6.8px;color:var(--footer-text)}
.f-email{left:395px;top:1073px;width:123px;height:21px;border:1px solid #555;font-size:6.8px;color:#bbb;padding:7px 8px}
.f-email svg{position:absolute;right:7px;top:7px}
.f-links{left:570px;top:1052px;list-style:none}
.f-links li{font-size:6.8px;line-height:14.8px;color:#bbb}
.f-links li::before{content:"»";color:#777;margin-right:6px}
.f-links li.on{color:var(--accent);text-decoration:underline}
.f-social{left:684px;top:1054px;display:flex;gap:3px}
.f-social span{width:17px;height:17px;border-radius:50%;border:1.3px solid #bbb}
.f-social span.on{border-color:var(--accent)}
</style>
</head>
<body>

<header class="site-header abs">
  <div class="brand abs"><span class="brand-dot"></span>Quillbrookes</div>
  <nav class="main-nav abs">
    <a class="active" href="#">Home</a><a href="#">Founder</a><a href="#">Consultancy</a><a href="#">Platform</a><a href="#">Case Studies</a><a href="#">Contact Us</a>
  </nav>
</header>

<section class="hero abs">
  <div class="hero-visual abs" role="img" aria-label="Glowing blue globe with light rays rising over the horizon"></div>
  <h2 class="hero-title abs">World Merchandising Trade 2012 ( USD Billion)</h2>
  <p class="hero-sub abs">We invest actively in developing technology platform for better distribution, disintermediation,<br>efficient process flow and cost effective delivery of solutions.</p>
  <svg class="hero-arrow abs" style="left:131px" width="12" height="22" viewBox="0 0 12 22"><path d="M10 1 1 11l9 10" fill="none" stroke="#fff" stroke-width="1.5"/></svg>
  <svg class="hero-arrow abs" style="left:841px" width="12" height="22" viewBox="0 0 12 22"><path d="M2 1l9 10-9 10" fill="none" stroke="#fff" stroke-width="1.5"/></svg>
  <div class="hero-dots abs"><span></span><span class="on"></span><span></span><span></span></div>
</section>

<section class="welcome abs">
  <h1>WELCOME TO <b>QUILLBROOKES</b></h1>
  <p class="tagline">WE BUILD LONG LASTING RELATIONSHIPS WITH ALL OUR <span>CLIENTS AND PARTNERS</span></p>
  <div class="divider"></div>
  <p class="intro">Quillbrookes Consultancy Limited capitalizes on synergies arising from trade and investment linkages between countries and knowledge of traditional and non-traditional pools of liquidity to provide consultancy services to Emerging country banks, Corporates and SMEs.</p>
  <span class="btn-contact">CONTACT US</span>
</section>

<div class="service abs" style="left:218px">
  <div class="icon"><svg width="26" height="26" viewBox="0 0 26 26" fill="#888"><rect x="2" y="17" width="5" height="8"/><rect x="9" y="13" width="5" height="12"/><rect x="16" y="9" width="5" height="16"/><path d="M2 14 10 7l4 3 8-8" fill="none" stroke="#888" stroke-width="2"/><path d="M18 1h6v6z"/></svg></div>
  <h3>Export Credit Agency</h3>
  <p>Quillbrookes Consultancy Limited (QCL) was exclusively appointed to arrange debt for this project.</p>
  <span class="more">read more</span>
</div>
<div class="service abs active" style="left:358px">
  <div class="icon"><svg width="34" height="30" viewBox="0 0 34 30" fill="var(--accent)"><circle cx="20" cy="5" r="4"/><circle cx="17" cy="15" r="5"/><path d="M1 18c5 0 8 3 12 5h9l10-7c1 2 0 4-2 5l-9 7H11L1 26z"/></svg></div>
  <h3>Regional/Local banks</h3>
  <p>Quillbrookes Consultancy Limited (QCL) was exclusively appointed to arrange debt for this project.</p>
  <span class="more">read more</span>
</div>
<div class="service abs" style="left:500px">
  <div class="icon"><svg width="26" height="26" viewBox="0 0 26 26"><circle cx="13" cy="13" r="11.5" fill="#888"/><path d="M13 1.5v23M1.5 13h23M6 4c4 5 4 13 0 18M20 4c-4 5-4 13 0 18" stroke="#fff" stroke-width="1.2" fill="none"/></svg></div>
  <h3>Structured Financing</h3>
  <p>Quillbrookes Consultancy Limited (QCL) was exclusively appointed to arrange debt for this project.</p>
  <span class="more">read more</span>
</div>
<div class="service abs" style="left:640px">
  <div class="icon"><svg width="28" height="28" viewBox="0 0 28 28"><circle cx="14" cy="14" r="13" fill="#888"/><path d="M14 14V1a13 13 0 0 1 10 4.5z" fill="#fff"/></svg></div>
  <h3>Bank Lines Business</h3>
  <p>Quillbrookes Consultancy Limited (QCL) was exclusively appointed to arrange debt for this project.</p>
  <span class="more">read more</span>
</div>

<section class="consult-band abs"></section>
<div class="band-heading abs"><h2>CONSULTANCY</h2></div>

<article class="card abs" style="left:220px">
  <div class="photo" role="img" aria-label="Three colleagues reviewing documents at a bright office desk" style="background:linear-gradient(135deg,#d8d4cf,#f2f1ef 45%,#5a8fc8)"><span class="go">→</span></div>
  <h4>BANK CONSULTANCY</h4>
  <p>The Consultancy provides access to local/regional banks across Hong Kong, Singapore, Dubai , New York and London</p>
</article>
<article class="card abs active" style="left:406px">
  <div class="photo" role="img" aria-label="Financial charts on paper with glasses and a pen" style="background:linear-gradient(160deg,#7a5a3e,#dfe7f0 35%,#bcd0e6 70%,#4a6a90)"><span class="go light">→</span></div>
  <h4>PLAIN VANILLA FINANCING SOLUTIONS</h4>
  <p>The Consultancy provides access to local/regional banks across Hong Kong, Singapore, Dubai , New York and London</p>
</article>
<article class="card abs" style="left:591px">
  <div class="photo" role="img" aria-label="Keyboard with a solution key beside a blue globe" style="background:linear-gradient(120deg,#c9d6e3,#8aa8c8 50%,#1f4f86)"><span class="go">→</span></div>
  <h4>STRUCTURED FINANCING SOLUTIONS</h4>
  <p>The Consultancy provides end-to-end structured solutions on the Payables, Receivables or Inventory side for working capital requirements</p>
</article>

<footer class="site-footer abs"></footer>
<div class="f-brand abs"><i></i>Quillbrookes</div>
<p class="f-address abs">Quillbrookes Consultancy Ltd<br>Suite 04, 9th Floor, Harbourline Tower,<br>28 Wexford Road, Kowloon<br>Hong Kong</p>
<p class="f-contact abs">T: <b>852-316 20584</b><br>E: &nbsp;<u>query@quill-brookes.com</u></p>

<h5 class="f-title abs" style="left:395px">GET IN TOUCH!</h5>
<p class="f-note abs">Simply Drop Your Mail Here</p>
<div class="f-email abs">Your Email Here<svg width="10" height="7" viewBox="0 0 10 7"><rect width="10" height="7" fill="var(--accent)"/><path d="M0 0l5 4 5-4" stroke="#1b1b1b" fill="none"/></svg></div>

<h5 class="f-title abs" style="left:570px">SITE LINKS</h5>
<ul class="f-links abs">
  <li class="on">Home</li><li>Founder</li><li>Consultancy</li><li>System</li><li>Case Studies</li><li>Contact</li>
</ul>

<h5 class="f-title abs" style="left:684px">SOCIAL LINKS</h5>
<div class="f-social abs"><span class="on"></span><span></span><span></span><span></span></div>

<div class="footer-bottom abs"><p>© 2016. Quillbrookes Consultancy Limited</p></div>

</body>
</html>
```